SkyvoTrade - where frequent flyers can cash out their airline miles

SkyvoTrade enable the trade of airline miles between individuals. Our landing page which I want to redesign should refer to individuals who have miles in airline loyalty programs and would like to sell them with our platform

I would like to get a landing page design with a look and feel much more advanced and appealing then the one we currently have.

Page should include the information and fields in our current landing page but should be more professional and include except for the current two partner's logos and our logo of course, also the attached banner of staynestly.example with a link to staynestly.example with our affiliate code.

Audience of our web page is business men and heavy travellers therefore, page should reflect professionalism and should be business wise. There could be something that has to do with airplanes and money in terms of the background and pictures shows.

Additional text (on top of the short description at skyvotrade.example is -
"
SkyvoTrade™ converts frequent flyers' accumulated miles to exceptionally low-priced flight tickets. It serves as an online trading platform for sellers of miles and buyers of flight tickets, offering airline customers a fully automated process whereby flight tickets are created out of loyalty club miles.
"

Our web site as a reference is www.skyvotrade.example

Target Market(s)

Business men who are heavily travellers

Industry/Entity Type

Travel Industry

Number of Pages Required

1 page

Font styles to use
Sans Serif

Colors
85acd3
0255a3

Requirements
Must have
• Our logo and the 3 logos mentioned at the description. It should have on the top the look & Feel that it currently has on our landing page - www.skyvotrade.example
Nice to have
• I would like people entering the web page to love it and for them to leave the relevant details so we get back to them
Should not have
• Not too many texts or images. Don't want people to scroll down too much if at all

```html
<!DOCTYPE html>
<html lang="en">
<head>
<meta charset="utf-8">
<title>SkyvoTrade – Sell your miles</title>
<link href="https://fonts.googleapis.com/css2?family=Open+Sans:wght@400;600;700&display=swap" rel="stylesheet">
<style>
  :root {
    --ink: #2b2b2b;
    --muted: #555;
    --brand-blue: #0a6aa8;
    --btn-top: #1a9be0;
    --btn-bottom: #0a6fb8;
    --btn-edge: #0255a3;
    --sky-top: #4f86c6;
    --sky-mid: #85acd3;
    --sky-low: #c9d8e6;
    --white: #ffffff;
    --line: #dcdcdc;
    --field-text: #555;
  }
  * { box-sizing: border-box; margin: 0; padding: 0; }
  html, body { width: 1200px; height: 1077px; overflow: hidden; }
  body { font-family: "Open Sans", sans-serif; color: var(--ink); background: var(--white); position: relative; }

  .top-strip { position: absolute; left: 0; top: 0; width: 1200px; height: 17px; background: #050505; }

  .hero { position: absolute; left: 0; top: 17px; width: 1200px; height: 658px;
    background: linear-gradient(180deg, var(--sky-top) 0%, var(--sky-mid) 45%, var(--sky-low) 78%, #8ea6bd 100%); }

  .brand { position: absolute; left: 99px; top: 38px; color: var(--white); }
  .brand-name { font-size: 34px; font-weight: 700; letter-spacing: -0.5px; line-height: 1; display: flex; align-items: center; gap: 8px; }
  .brand-mark { width: 14px; height: 14px; background: var(--white); display: inline-block; }
  .brand-tag { font-size: 12px; font-weight: 600; margin-top: 8px; margin-left: 98px; }

  .nav { position: absolute; top: 50px; left: 0; font-size: 12px; font-weight: 700; color: var(--white); }
  .nav span { position: absolute; white-space: nowrap; }

  .intro { position: absolute; left: 99px; top: 470px; width: 460px; }
  .intro h1 { font-size: 45px; font-weight: 700; color: var(--brand-blue); letter-spacing: -0.5px; line-height: 1.1; }
  .intro p { font-size: 15.5px; line-height: 29px; margin-top: 8px; color: #1e1e1e; }

  .sell-form { position: absolute; left: 632px; top: 0; width: 470px; color: var(--white); }
  .sell-form h2 { position: absolute; top: 140px; font-size: 45px; font-weight: 400; white-space: nowrap; }
  .sell-form h3 { position: absolute; font-size: 19px; font-weight: 400; white-space: nowrap; }
  .field { position: absolute; width: 229px; height: 35px; background: var(--white);
    border: 1px solid #d7dde3; border-radius: 2px; font-size: 11px; color: var(--field-text);
    padding-left: 15px; line-height: 33px; }
  .submit { position: absolute; left: 0; top: 527px; width: 230px; height: 45px; border-radius: 3px;
    background: linear-gradient(180deg, var(--btn-top), var(--btn-bottom)); border-bottom: 2px solid var(--btn-edge);
    color: var(--white); font-size: 17px; font-weight: 700; text-align: center; line-height: 43px; }

  .banner { position: absolute; left: 127px; top: 712px; width: 214px; height: 214px; overflow: hidden;
    background: linear-gradient(180deg, #10388a 0%, #1c55a8 26%, #7fb6d4 40%, #e9e3d3 62%, #3d8fc1 80%, #2b6f9f 100%); color: var(--white); text-align: center; }
  .banner-title { font-size: 16px; margin-top: 9px; }
  .banner-sub { font-size: 10.5px; margin-top: 1px; }
  .banner-cta { position: absolute; left: 70px; top: 152px; width: 74px; height: 25px; background: #1a8fe0;
    border: 1px solid var(--white); font-size: 12px; line-height: 23px; }
  .banner-brand { position: absolute; left: 0; width: 100%; top: 183px; font-size: 16px; font-weight: 700; }

  .welcome { position: absolute; left: 398px; top: 720px; width: 640px; }
  .welcome h2 { font-size: 27px; font-weight: 400; color: var(--muted); }
  .welcome h2 strong { font-weight: 700; }
  .welcome p { font-size: 13px; line-height: 26.6px; color: var(--muted); margin-top: 6px; padding-left: 3px; }
  .contact-btn { position: absolute; left: 400px; top: 866px; width: 145px; height: 41px; border-radius: 3px;
    background: linear-gradient(180deg, var(--btn-top), var(--btn-bottom)); border-bottom: 2px solid var(--btn-edge);
    color: var(--white); font-size: 14.5px; font-weight: 700; text-align: center; line-height: 39px; }

  .footer-rule { position: absolute; left: 0; top: 974px; width: 1200px; height: 1px; background: var(--line); }
  .footer-text { position: absolute; top: 1014px; font-size: 11px; color: var(--muted); white-space: nowrap; }
  .social { position: absolute; top: 1005px; width: 34px; height: 34px; border-radius: 50%; }
  .partner { position: absolute; top: 1012px; font-size: 17px; font-weight: 700; white-space: nowrap; display: flex; align-items: center; gap: 6px; }
  .partner-box { width: 20px; height: 20px; background: #4a5a66; display: inline-block; border-radius: 3px; }
</style>
</head>
<body>
  <div class="top-strip"></div>

  <section class="hero" role="img" aria-label="Passenger jet flying over snowy mountains under a blue sky">
    <div class="brand">
      <div class="brand-name">SkyvoTrade <span class="brand-mark"></span></div>
      <div class="brand-tag">Loyalty Pays</div>
    </div>

    <nav class="nav">
      <span style="left:803px">HOME</span>
      <span style="left:902px">ABOUT US</span>
      <span style="left:1025px">CONTACT US</span>
    </nav>

    <div class="intro">
      <h1>SkyvoTrade™</h1>
      <p>converts frequent flyers' accumulated miles to exceptionally low-priced flight tickets.</p>
    </div>

    <form class="sell-form">
      <h2>Sell your miles</h2>
      <h3 style="top:204px">Personal Details</h3>
      <div class="field" style="left:0;top:241px">First Name</div>
      <div class="field" style="left:240px;top:241px">Last Name</div>
      <div class="field" style="left:0;top:288px">Email</div>
      <div class="field" style="left:240px;top:288px">Phone</div>
      <h3 style="top:350px">Airlines Details</h3>
      <div class="field" style="left:0;top:387px">Airline #1</div>
      <div class="field" style="left:240px;top:387px">Amount of Miles</div>
      <div class="field" style="left:0;top:434px">Airline #2</div>
      <div class="field" style="left:240px;top:434px">Amount of Miles</div>
      <div class="field" style="left:0;top:479px">Airline #3</div>
      <div class="field" style="left:240px;top:479px">Amount of Miles</div>
      <div class="submit">Submit now</div>
    </form>
  </section>

  <aside class="banner" role="img" aria-label="Beach resort with parasols and a pool, holiday booking banner">
    <div class="banner-title">Vacation of a Lifetime</div>
    <div class="banner-sub">Book a slice of paradise</div>
    <div class="banner-cta">Book now</div>
    <div class="banner-brand">Staynestly</div>
  </aside>

  <section class="welcome">
    <h2>Welcome to <strong>SkyvoTrade™</strong></h2>
    <p>SkyvoTrade™ converts frequent flyers' accumulated miles to exceptionally low-priced flight tickets. It serves as an online trading platform for sellers of miles and buyers of flight tickets, offering airline customers a fully automated process whereby flight tickets are created out of loyalty club miles. "</p>
  </section>
  <div class="contact-btn">Contact now</div>

  <div class="footer-rule"></div>
  <div class="footer-text" style="left:99px">Copyright © 2015. SkyvoTrade™. All rights reserved.</div>
  <div class="footer-text" style="left:363px">Terms &amp; Conditions</div>
  <div class="footer-text" style="left:483px">/</div>
  <div class="footer-text" style="left:505px">Privacy Policy</div>

  <div class="social" style="left:598px;background:#2a6fc0"></div>
  <div class="social" style="left:641px;background:#1a7fae"></div>
  <div class="social" style="left:684px;background:#3ab0e8"></div>
  <div class="social" style="left:726px;background:#3a3a3a"></div>

  <div class="partner" style="left:860px;color:#d4202a">Orvane Tours</div>
  <div class="partner" style="left:1010px;color:#4a5a66"><span class="partner-box"></span>Brightwire Hub</div>
</body>
</html>
```